A4 Single Sided Brochure Folder Design Technical Company

We are a technical company based in the UK, working worldwide for Power Distribution companies.

We have technical literature and need a folder to present these in. The design should be very simple and clean using our logo and "Innovative Utility Solutions"

Our website kestrome.com gives and idea of the business but don't follow the look of the website as we will be redoing shortly.

• Logo and Strap Line
• Clean, easy to print and timeless
• Shouldn't be fashionable, we certainly aren't

```html
<!DOCTYPE html>
<html lang="en">
<head>
<meta charset="utf-8">
<title>Kestrome Presentation Folder</title>
<link rel="stylesheet" href="https://fonts.googleapis.com/css2?family=Lato:wght@300;400&display=swap">
<style>
  :root {
    --magenta: #b92e8a;
    --paper: #ffffff;
    --backdrop: #d9d5d0;
    --ink-grey: #5a5a5a;
    --url-grey: #8a8a8a;
    --fold-line: #b8aca4;
  }
  html, body {
    margin: 0;
    padding: 0;
    width: 1200px;
    height: 1200px;
    overflow: hidden;
    background: var(--backdrop);
  }
  .canvas {
    position: relative;
    width: 1200px;
    height: 1200px;
    font-family: "Lato", sans-serif;
  }
  .folder-outline {
    position: absolute;
    left: 0;
    top: 0;
  }
  .cover-panel {
    position: absolute;
    left: 109px;
    top: 142px;
    width: 1016px;
    height: 540px;
    background: var(--magenta);
  }
  .brand-name {
    position: absolute;
    left: 738px;
    top: 575px;
    margin: 0;
    font-weight: 300;
    font-size: 72px;
    line-height: 1;
    letter-spacing: 1px;
    color: var(--paper);
  }
  .strapline {
    position: absolute;
    left: 726px;
    top: 714px;
    margin: 0;
    font-weight: 300;
    font-size: 26px;
    color: var(--ink-grey);
    white-space: nowrap;
  }
  .web-address {
    position: absolute;
    left: 318px;
    top: 722px;
    margin: 0;
    font-weight: 300;
    font-size: 12px;
    color: var(--url-grey);
  }
</style>
</head>
<body>
<div class="canvas">
  <svg class="folder-outline" width="1200" height="1200" viewBox="0 0 1200 1200" aria-hidden="true">
    <rect class="folder-body" x="109" y="142" width="1016" height="710" fill="#ffffff"/>
    <polygon class="pocket-flap" points="109,852 617,852 546,1062 109,1062" fill="#ffffff"/>
    <polygon class="glue-tab" points="74,862 109,852 109,1062 74,1058" fill="#ffffff"/>
    <line class="fold-line" x1="109" y1="852" x2="617" y2="852" stroke="var(--fold-line)" stroke-width="0.8"/>
    <line class="fold-line" x1="109" y1="852" x2="109" y2="1062" stroke="var(--fold-line)" stroke-width="0.8"/>
  </svg>

  <div class="cover-panel"></div>
  <h1 class="brand-name">Kestrome</h1>
  <p class="strapline">Innovative Utility Solutions</p>
  <p class="web-address">www.kestrome.com</p>
</div>
</body>
</html>
```